Looking for a modern, Professional business card design

We have a simple business card, but are looking for a more modern, professional look. A sample of the basic card is attached as well as the logo. We would also like to add that we offer:
Struggling with your finances?
- Learn to become debt free
- Discover the power of cash
- Control your money instead of it controlling you
Let us help you achieve a new level of financial freedom!
Also, we would like to have a "SPECIAL OFFER!: FREE 30 minute consultation"
Financial Planning

```html
<!DOCTYPE html>
<html lang="en">
<head>
<meta charset="utf-8">
<title>Clearpath Money Coaching – Business Card</title>
<link href="https://fonts.googleapis.com/css2?family=Open+Sans:wght@400;600;700&display=swap" rel="stylesheet">
<style>
  :root {
    --backdrop: #3a332f;
    --card: #0d0d0d;
    --green: #8cc63f;
    --green-bright: #9bd431;
    --white: #f2f2f2;
    --divider: #2a2a2a;
  }
  * { margin: 0; padding: 0; box-sizing: border-box; }
  html, body { width: 1200px; height: 900px; overflow: hidden; }
  body {
    background: var(--backdrop);
    font-family: "Open Sans", Arial, sans-serif;
    position: relative;
  }
  .card {
    position: absolute;
    width: 540px;
    height: 310px;
    background: var(--card);
    border-radius: 4px;
    box-shadow: 0 10px 30px rgba(0,0,0,.45);
    color: var(--white);
  }
  .card--front { left: 40px; top: 300px; }
  .card--back  { left: 620px; top: 300px; }

  /* front */
  .brand-mark {
    position: absolute; left: 30px; top: 0; width: 210px; height: 100%;
    display: flex; align-items: center; gap: 10px;
  }
  .brand-mark__dot { width: 18px; height: 18px; border-radius: 50%; background: var(--green); flex: none; }
  .brand-mark__name { color: var(--green); font-weight: 700; font-size: 20px; line-height: 1.15; }
  .card__divider {
    position: absolute; left: 250px; top: 70px; width: 1px; height: 170px;
    background: var(--divider);
  }
  .contact { position: absolute; left: 272px; top: 78px; }
  .contact__name { color: var(--green); font-weight: 700; font-size: 17px; }
  .contact__role { font-size: 14px; margin-bottom: 28px; }
  .contact__list { list-style: none; font-size: 14px; line-height: 22px; }
  .contact__list li { display: flex; align-items: center; gap: 10px; }
  .contact__list svg { width: 11px; height: 11px; fill: var(--green); flex: none; }

  /* back */
  .back-brand {
    position: absolute; left: 0; right: 0; top: 34px;
    display: flex; justify-content: center; align-items: center; gap: 10px;
  }
  .back-brand .brand-mark__name { font-size: 22px; }
  .pitch { position: absolute; left: 60px; right: 40px; top: 100px; }
  .pitch__question { color: var(--green); font-weight: 700; font-size: 15px; margin-bottom: 8px; }
  .pitch__list { list-style: none; font-size: 13.5px; line-height: 20px; margin-bottom: 10px; }
  .pitch__list li { display: flex; align-items: center; gap: 8px; padding-left: 28px; }
  .pitch__list li:last-child { padding-left: 0; }
  .pitch__list svg { width: 8px; height: 9px; fill: var(--green); flex: none; }
  .pitch__close { font-size: 13.5px; margin-bottom: 12px; }
  .pitch__offer { color: var(--green-bright); font-weight: 600; font-size: 16.5px; letter-spacing: .2px; }
</style>
</head>
<body>

<section class="card card--front" aria-label="Business card front">
  <div class="brand-mark">
    <span class="brand-mark__dot"></span>
    <span class="brand-mark__name">Clearpath Money Coaching</span>
  </div>
  <div class="card__divider"></div>
  <div class="contact">
    <p class="contact__name">Daniel R. Hayes</p>
    <p class="contact__role">Personal financial coach</p>
    <ul class="contact__list">
      <li><svg viewBox="0 0 10 10"><path d="M2 0h2l1 3-1.4 1a6 6 0 0 0 2.4 2.4L7 5l3 1v2a2 2 0 0 1-2 2A8 8 0 0 1 0 2a2 2 0 0 1 2-2z"/></svg>(555) 010-2387</li>
      <li><svg viewBox="0 0 10 10"><path d="M0 2h10v6H0z M0 2l5 3.5L10 2" stroke="#0d0d0d" stroke-width=".8"/></svg>daniel@clearpathmoney.com</li>
      <li><svg viewBox="0 0 10 10"><circle cx="5" cy="5" r="5"/></svg>www.clearpathmoney.com</li>
    </ul>
  </div>
</section>

<section class="card card--back" aria-label="Business card back">
  <div class="back-brand">
    <span class="brand-mark__dot"></span>
    <span class="brand-mark__name">Clearpath Money Coaching</span>
  </div>
  <div class="pitch">
    <p class="pitch__question">Struggling with your finances?</p>
    <ul class="pitch__list">
      <li><svg viewBox="0 0 8 9"><path d="M0 0l8 4.5L0 9z"/></svg>Learn to become debt free</li>
      <li><svg viewBox="0 0 8 9"><path d="M0 0l8 4.5L0 9z"/></svg>Discover the power of cash</li>
      <li><svg viewBox="0 0 8 9"><path d="M0 0l8 4.5L0 9z"/></svg>Control your money instead of it controlling you</li>
    </ul>
    <p class="pitch__close">Let us help you achieve a new level of financial freedom!</p>
    <p class="pitch__offer">SPECIAL OFFER!: FREE 30 MINUTE CONSULTATION</p>
  </div>
</section>

</body>
</html>
```